Marwick Law Letterhead

We need a new letterhead design for a Law Firm. The address for the law firm is 1475 Calloway Street, Suite 210, Houston, Texas 77041. Phone Number: 832-361-9027; Fax Number: 832-614-7359. The logo is uploaded to the project.

```html
<!DOCTYPE html>
<html lang="en">
<head>
<meta charset="utf-8">
<title>Marwick Law Letterhead</title>
<link href="https://fonts.googleapis.com/css2?family=Roboto:wght@400;500&display=swap" rel="stylesheet">
<style>
  :root {
    --bg: #dcdcdc;
    --paper: #f1f1f0;
    --navy: #14264f;
    --navy-deep: #0d1d3d;
    --red: #8e1218;
    --red-bright: #d41f27;
    --ink: #2a2a2a;
    --sig: #e2e2e0;
  }
  * { margin: 0; padding: 0; box-sizing: border-box; }
  html, body { width: 1069px; height: 1200px; overflow: hidden; background: var(--bg); }
  body { position: relative; font-family: "Roboto", sans-serif; color: var(--ink); }

  .letterhead {
    position: absolute; left: 125px; top: 21px;
    width: 819px; height: 1157px;
    background: var(--paper);
    box-shadow: 0 10px 30px rgba(0,0,0,0.18);
    overflow: hidden;
  }
  .band-top { position: absolute; left: 0; top: 0; width: 100%; height: 15px; display: flex; }
  .band-top .navy { width: 50%; background: var(--navy-deep); }
  .band-top .red { width: 50%; background: linear-gradient(90deg, var(--red), var(--red-bright)); }

  .brand-mark { position: absolute; left: 46px; top: 74px; width: 72px; height: 72px; background: var(--navy); }
  .brand-name {
    position: absolute; left: 139px; top: 86px;
    font-size: 40px; font-weight: 500; color: var(--navy); line-height: 1; letter-spacing: 0.3px;
  }
  .brand-tagline {
    position: absolute; left: 139px; top: 148px;
    font-size: 8.6px; letter-spacing: 1.2px; color: var(--red-bright); text-transform: uppercase;
  }

  .contact-rule { position: absolute; left: 575px; top: 66px; width: 1.5px; height: 108px; background: var(--navy); }
  .contact { position: absolute; left: 593px; top: 60px; font-size: 16.5px; line-height: 20.7px; color: #1d1d1d; font-style: normal; }
  .contact-line { position: absolute; left: 593px; font-size: 16.5px; line-height: 20px; display: flex; align-items: center; gap: 5px; color: #1d1d1d; }
  .contact-line svg { width: 14px; height: 14px; fill: var(--red-bright); }
  .phone { top: 130px; }
  .fax { top: 157px; }

  .recipient { position: absolute; left: 46px; top: 326px; font-size: 14.6px; line-height: 23.7px; }
  .body-copy { position: absolute; left: 46px; width: 727px; font-size: 14.5px; line-height: 23.6px; text-align: justify; hyphens: auto; }
  .p1 { top: 437px; }
  .p2 { top: 581px; }
  .p3 { top: 719px; }
  .closing { position: absolute; left: 46px; top: 829px; font-size: 14.6px; line-height: 23.6px; }
  .signature { position: absolute; left: 46px; top: 867px; width: 148px; height: 59px; background: var(--sig); border-radius: 4px; }

  .band-bottom { position: absolute; left: 0; top: 1124px; width: 100%; height: 33px; display: flex; }
  .band-bottom .navy { width: 50%; background: linear-gradient(90deg, var(--navy), var(--navy-deep)); }
  .band-bottom .red { width: 50%; background: linear-gradient(90deg, var(--red), var(--red-bright)); }
  .band-dot { position: absolute; left: 391px; top: 1122px; width: 37px; height: 37px; border-radius: 50%; background: var(--paper); }
</style>
</head>
<body>
  <main class="letterhead">
    <div class="band-top"><div class="navy"></div><div class="red"></div></div>

    <div class="brand-mark"></div>
    <div class="brand-name">Marwick Law</div>
    <div class="brand-tagline">Standing with you after every injury</div>

    <div class="contact-rule"></div>
    <address class="contact">1475 Calloway Street<br>Suite 210, Houston,<br>Texas 77041</address>
    <div class="contact-line phone">
      <svg viewBox="0 0 24 24" aria-hidden="true"><path d="M2 9c0-3 5-5 10-5s10 2 10 5v2h-5V8.5c-1.5-.6-3.3-.9-5-.9s-3.5.3-5 .9V11H2zM6 12l2-3h8l2 3 2 8H4z"/></svg>
      <span>832-361-9027</span>
    </div>
    <div class="contact-line fax">
      <svg viewBox="0 0 24 24" aria-hidden="true"><path d="M6 2h12v6H6zM3 9h18v9h-3v-3H6v3H3zM7 16h10v6H7z"/></svg>
      <span>832-614-7359</span>
    </div>

    <div class="recipient">Mr/s<br>First Name and Last Name<br>Company Name<br>Address</div>

    <p class="body-copy p1" lang="en">Lorem Ipsum is simply dummy text of the printing and typesetting industry. Lorem Ipsum has been the industry's standard dummy text ever since the 1500s, when an unknown printer took a galley of type and scrambled it to make a type specimen book. It has survived not only five centuries, but also the leap into electronic typesetting, remaining essentially unchanged. It was popularised in the 1960s with the release of Presstype sheets containing Lorem Ipsum passages.</p>

    <p class="body-copy p2" lang="en">he standard chunk of Lorem Ipsum used since the 1500s is reproduced below for those interested. Sec&shy;tions 1.10.32 and 1.10.33 from "de Finibus Bonorum et Malorum" by Lucan Varro are also reproduced in their exact original form, accompanied by English versions from the 1914 translation by H. Bramley. Lorem ipsum dolor sit amet, consectetur adipiscing elit, sed do eiusmod tempor incididunt ut labore et dolore magna aliqua.</p>

    <p class="body-copy p3" lang="en">It is a long established fact that a reader will be distracted by the readable content of a page when look&shy;ing at its layout. The point of using Lorem Ipsum is that it has a more-or-less normal distribution of letters, as opposed to using 'Content here, content here', making it look like readable English. Many desktop publishing packages and web page editors now .</p>

    <div class="closing">Your Sincerely,</div>
    <div class="signature" role="img" aria-label="Handwritten signature"></div>

    <div class="band-bottom"><div class="navy"></div><div class="red"></div></div>
    <div class="band-dot"></div>
  </main>
</body>
</html>
```